Business Card Re-Design/Update

We'd like to update out business cards. I've included our current "Style guide" which has the colour scheme of the organisation in it. I've also included the branding files with logos etc in them.

I've also included a copy of one of our existing cards so that you can see how ugly/dated they look. I'd like a fresh modern corporate look.

Target Market(s)

These are for our clients, potential clients, industry contacts - like all business cards

Contact Information for Business Card

Name
Position
Company Address - Level 1, 47 Fernby Street, Carlow Qld 4072
Direct Phone
mobile
Email
Website -www.korvalit.com.au
Logo

Colors

Designer to choose colors to be used in the design.

Requirements
Must have
• Main Logo
• Cards will need to be editable to be able to personalize them for each new employee.
Nice to have
• The MapOut, ShipWell, KeepSteady would be okay to have if they can be sensibly and professionally added to the look without detracting from the main imagery.
• Maybe they could go on the back of the card? will leave this to your creative discretion as to whether/where they fit.
Should not have
• Should not have decorative or script fonts

```html
<!DOCTYPE html>
<html lang="en">
<head>
<meta charset="utf-8">
<title>Korvalit Business Card</title>
<link rel="stylesheet" href="https://fonts.googleapis.com/css2?family=Montserrat:wght@600;700&family=Arimo:wght@400&display=swap">
<style>
  :root {
    --brand-red: #d71920;
    --ink: #3a3a3c;
    --ink-soft: #555557;
    --band-grey: #3d3d40;
    --card-white: #ffffff;
    --backdrop: #e4e4e6;
  }
  * { box-sizing: border-box; margin: 0; padding: 0; }
  html, body { width: 1200px; height: 782px; overflow: hidden; }
  body {
    background: var(--backdrop);
    font-family: "Arimo", Arial, sans-serif;
    color: var(--ink);
    position: relative;
  }
  .card {
    position: absolute;
    top: 241px;
    width: 525px;
    height: 300px;
    overflow: hidden;
    box-shadow: 0 6px 18px rgba(0,0,0,0.18);
  }
  .card--front { left: 50px; background: var(--card-white); }
  .card--back { left: 625px; background: var(--brand-red); }

  .front-shapes { position: absolute; inset: 0; }

  .holder { position: absolute; left: 46px; top: 24px; }
  .holder-name {
    font-family: "Montserrat", Arial, sans-serif;
    font-weight: 700;
    font-size: 16px;
    letter-spacing: 0.3px;
    color: var(--brand-red);
    text-transform: uppercase;
  }
  .holder-role { font-size: 12px; color: var(--ink-soft); margin-top: 1px; }

  .contact-list { position: absolute; left: 26px; top: 120px; list-style: none; }
  .contact-list li {
    display: flex; align-items: center; gap: 7px;
    font-size: 12.5px; line-height: 17px; color: var(--ink);
  }
  .contact-list svg { width: 10px; height: 10px; fill: var(--brand-red); flex: none; }

  .brand {
    position: absolute; left: 300px; top: 150px;
    display: flex; align-items: center; gap: 10px;
  }
  .brand-square { width: 26px; height: 26px; background: var(--brand-red); }
  .brand-name {
    font-family: "Montserrat", Arial, sans-serif;
    font-weight: 600;
    font-size: 36px;
    color: var(--ink);
    letter-spacing: -0.5px;
  }

  .address {
    position: absolute; right: 26px; top: 222px;
    text-align: right; font-size: 13px; line-height: 17px; color: var(--ink);
  }

  .back-field { position: absolute; inset: 0; background: var(--brand-red); }
  .back-brand {
    position: absolute; right: 40px; bottom: 60px;
    display: flex; align-items: center; gap: 8px;
  }
  .back-brand .brand-square { width: 20px; height: 20px; background: var(--card-white); }
  .back-brand .brand-name { color: var(--card-white); font-size: 24px; }
</style>
</head>
<body>

<section class="card card--front" aria-label="Card front">
  <svg class="front-shapes" viewBox="0 0 525 300" aria-hidden="true">
    <polygon points="0,20 36,20 30,48 0,48" fill="var(--brand-red)"/>
    <line x1="0" y1="52" x2="28" y2="52" stroke="var(--band-grey)" stroke-width="2"/>
    <polygon points="0,280 225,280 217,300 0,300" fill="var(--band-grey)"/>
    <polygon points="240,274 525,274 525,300 230,300" fill="var(--brand-red)"/>
  </svg>

  <div class="holder">
    <p class="holder-name">Dana Whitmore</p>
    <p class="holder-role">Business Development Manager</p>
  </div>

  <ul class="contact-list">
    <li><svg viewBox="0 0 10 10"><path d="M1 3C1 2 2 1 3 1h4c1 0 2 1 2 2v1H7V3H3v1H1z M2 5h6l1 4H1z"/></svg>+61 (0)412 555 019</li>
    <li><svg viewBox="0 0 10 10"><path d="M3 0h4a1 1 0 0 1 1 1v8a1 1 0 0 1-1 1H3a1 1 0 0 1-1-1V1a1 1 0 0 1 1-1zM3 1.5v6h4v-6z"/></svg>+61 (0)7 5550 1842</li>
    <li><svg viewBox="0 0 10 10"><path d="M2 0h6v3H2zM0 3.5h10V8H8v2H2V8H0zM3 6.5v2.5h4V6.5z"/></svg>+61 (0)7 5550 1843</li>
    <li><svg viewBox="0 0 10 10"><path d="M0 2h10v6H0zM1 3v.4l4 2.6 4-2.6V3L5 5.4z"/></svg>dwhitmore@korvalit.com.au</li>
    <li><svg viewBox="0 0 10 10"><circle cx="5" cy="5" r="5"/></svg>www.korvalit.com.au</li>
  </ul>

  <div class="brand">
    <span class="brand-square" aria-hidden="true"></span>
    <span class="brand-name">korvalit</span>
  </div>

  <address class="address" style="font-style:normal">
    Level 1, 47 Fernby Street<br>Carlow Qld 4072
  </address>
</section>

<section class="card card--back" aria-label="Card back">
  <div class="back-field" role="img" aria-label="Red field with a faint repeating brand-mark pattern"></div>
  <div class="back-brand">
    <span class="brand-square" aria-hidden="true"></span>
    <span class="brand-name">korvalit</span>
  </div>
</section>

</body>
</html>
```